we need a design for Water Bottle Lable Wrap
The product is called Calmora Springs is a restructured water. its a very healthy and rejuvenating water
we were looking at using as a tag ling Refresh, Renew, Rebalance.

```html
<!DOCTYPE html>
<html lang="en">
<head>
<meta charset="utf-8">
<title>Calmora Springs – Label Wrap</title>
<link href="https://fonts.googleapis.com/css2?family=Josefin+Sans:wght@600&family=Montserrat:wght@500&display=swap" rel="stylesheet">
<style>
  :root {
    --page-bg: #ffffff;
    --ink: #4a5275;
    --water-light: #f2f9fe;
    --water-mid: #7cc0ea;
    --water-deep: #1d78bb;
    --water-dark: #0f5d9c;
  }
  html, body {
    margin: 0;
    padding: 0;
    width: 1200px;
    height: 1200px;
    overflow: hidden;
    background: var(--page-bg);
  }
  .canvas {
    position: relative;
    width: 1200px;
    height: 1200px;
  }
  .label-wrap {
    position: absolute;
    left: 300px;
    top: 160px;
    width: 600px;
    height: 880px;
    overflow: hidden;
  }
  .splash-photo {
    position: absolute;
    inset: 0;
    background:
      radial-gradient(ellipse 40% 70% at 72% 55%, rgba(255,255,255,0.45), rgba(255,255,255,0) 70%),
      linear-gradient(180deg, rgba(255,255,255,0.55) 0%, rgba(255,255,255,0) 45%, rgba(15,93,156,0.25) 100%),
      linear-gradient(90deg, var(--water-light) 0%, var(--water-mid) 45%, var(--water-deep) 85%, var(--water-dark) 100%);
  }
  .brand-name {
    position: absolute;
    left: 250px;
    top: 445px;
    transform: translate(-50%, -50%) rotate(-90deg);
    font-family: "Josefin Sans", sans-serif;
    font-weight: 600;
    font-size: 180px;
    line-height: 1;
    letter-spacing: -2px;
    color: var(--ink);
    white-space: nowrap;
    margin: 0;
  }
  .tagline {
    position: absolute;
    left: 367px;
    top: 441px;
    transform: translate(-50%, -50%) rotate(-90deg);
    font-family: "Montserrat", sans-serif;
    font-weight: 500;
    font-size: 18px;
    line-height: 1;
    letter-spacing: 2.5px;
    color: var(--ink);
    white-space: nowrap;
    margin: 0;
  }
</style>
</head>
<body>
  <main class="canvas">
    <section class="label-wrap">
      <div class="splash-photo" role="img" aria-label="Photograph of a clear blue water splash rising against a soft blue background"></div>
      <h1 class="brand-name">calmora</h1>
      <p class="tagline">REFRESH, RENEW, REBALANCE</p>
    </section>
  </main>
</body>
</html>
```